Lumavento business card

We need a modern business card - With our 4 colors - See web: www.lumavento.dk

I have attached logo and som old business Cards we have - Lets Make the new ones shine...:-) -

Industry/Entity Type

Business

Requirements
Must have
• the logo with lumavento only,

```html
<!DOCTYPE html>
<html lang="da">
<head>
<meta charset="utf-8">
<title>Lumavento business card</title>
<link href="https://fonts.googleapis.com/css2?family=Josefin+Sans:wght@300;400;600&display=swap" rel="stylesheet">
<style>
  :root {
    --backdrop: #e9e6e1;
    --card: #141414;
    --lime: #8fd14f;
    --pink: #d63a96;
    --orange: #e8883a;
    --purple: #6e2a80;
  }
  html, body {
    margin: 0;
    width: 1200px;
    height: 1023px;
    overflow: hidden;
    background: var(--backdrop);
    font-family: "Josefin Sans", sans-serif;
  }
  .card {
    position: absolute;
    left: 250px;
    width: 700px;
    height: 400px;
    background: var(--card);
    box-shadow: 0 10px 28px rgba(0,0,0,.25);
    overflow: hidden;
  }
  .card-front { top: 70px; }
  .card-back { top: 553px; }

  /* front */
  .identity {
    position: absolute;
    left: 62px;
    top: 192px;
  }
  .brand {
    display: flex;
    align-items: center;
    gap: 11px;
    color: var(--orange);
    font-weight: 300;
    font-size: 33px;
    letter-spacing: 1px;
    line-height: 1;
  }
  .brand-dot {
    width: 24px;
    height: 24px;
    border-radius: 50%;
    background: var(--lime);
  }
  .rule {
    width: 256px;
    height: 2px;
    background: var(--lime);
    margin: 12px 0 12px;
  }
  .person-name {
    color: var(--orange);
    font-weight: 300;
    font-size: 29px;
    line-height: 1.1;
    margin: 0;
  }
  .person-title {
    color: var(--pink);
    font-weight: 600;
    font-size: 22px;
    line-height: 1.1;
    margin: 6px 0 0 34px;
  }
  .timeline {
    position: absolute;
    left: 402px;
    top: 0;
    width: 6px;
    height: 400px;
  }
  .timeline span { position: absolute; left: 0; width: 100%; }
  .seg-pink { top: 0; height: 156px; background: var(--pink); }
  .seg-lime { top: 156px; height: 108px; background: var(--lime); }
  .seg-orange { top: 264px; height: 117px; background: var(--orange); }
  .seg-purple { top: 381px; height: 19px; background: var(--purple); }
  .contact-icon {
    position: absolute;
    left: 385px;
    width: 40px;
    height: 40px;
    border-radius: 50%;
    display: flex;
    align-items: center;
    justify-content: center;
  }
  .contact-icon svg { width: 20px; height: 20px; }
  .icon-address { top: 88px; background: var(--pink); }
  .icon-phone { top: 198px; background: var(--lime); }
  .icon-mail { top: 307px; background: var(--orange); }
  .contact-text {
    position: absolute;
    left: 460px;
    color: var(--lime);
    font-weight: 400;
    font-size: 21px;
    line-height: 30px;
    margin: 0;
    letter-spacing: .4px;
  }
  .text-address { top: 79px; }
  .text-phone { top: 189px; }
  .text-mail { top: 298px; }

  /* back */
  .block { position: absolute; width: 52px; height: 88px; }
  .block-purple { left: 0; top: 0; background: var(--purple); }
  .block-green { left: 0; top: 88px; background: var(--lime); }
  .block-pink { right: 0; top: 224px; background: var(--pink); }
  .block-orange { right: 0; top: 312px; background: var(--orange); }
</style>
</head>
<body>
  <section class="card card-front" aria-label="Lumavento business card, front">
    <div class="identity">
      <div class="brand"><span class="brand-dot"></span><span>lumavento</span></div>
      <div class="rule"></div>
      <p class="person-name">Rasmus Holmgaard</p>
      <p class="person-title">Salgsdrictor</p>
    </div>

    <div class="timeline">
      <span class="seg-pink"></span>
      <span class="seg-lime"></span>
      <span class="seg-orange"></span>
      <span class="seg-purple"></span>
    </div>

    <div class="contact-icon icon-address">
      <svg viewBox="0 0 24 24"><path d="M4 5 L21 12 L4 19 L8 12 Z" fill="#141414"/></svg>
    </div>
    <div class="contact-icon icon-phone">
      <svg viewBox="0 0 24 24"><path d="M3 9 Q12 3 21 9 L19 12 L16 10 L16 8 Q12 6.5 8 8 L8 10 L5 12 Z M6 14 L18 14 L19 20 L5 20 Z" fill="#141414"/><circle cx="12" cy="17" r="2" fill="#8fd14f"/></svg>
    </div>
    <div class="contact-icon icon-mail">
      <svg viewBox="0 0 24 24"><rect x="3" y="6" width="18" height="12" fill="#141414"/><path d="M3 6 L12 13 L21 6" stroke="#e8883a" stroke-width="1.5" fill="none"/></svg>
    </div>

    <p class="contact-text text-address">Kastanje Allé 41<br>2000 Frederiksberg</p>
    <p class="contact-text text-phone">+45 31 42 67 08<br>+45 60 17 83 52</p>
    <p class="contact-text text-mail">rh@lumavento.dk<br>info@lumavento.dk</p>
  </section>

  <section class="card card-back" aria-label="Lumavento business card, back">
    <span class="block block-purple"></span>
    <span class="block block-green"></span>
    <span class="block block-pink"></span>
    <span class="block block-orange"></span>
  </section>
</body>
</html>
```